Business Card Design

Hi I need a business card designed, we already have the business name logo artwork and would like some concept ideas for the Bus Card layout.
On the back of the card i want to include the products and services that we offer.
We are a Plastics Sheeting manufacture based in Perth Australia.

                                       

We need a BC design for a company called Tarvo Plastics based in Perth Australia.

We supply from DIY to Trade & Industrial  Engineering Markets.

We specialise in:

·         Cut to size panels  (all shapes and sizes)

·         Plastics fabrication & Welding

·         Custom Designs

·         Plastic Repairs

·         PVC Pipe Slotting & PVC Pipe Threading

·         Supplier of all types of engineering plastics and profiles.

Including:           Acrylic / Clarvene

                               Polycarbonate / Dorvil

                               Prismatic Light Diffuser

                               Vantrib

                               HDPE / UHMWPE

                               PVC / PVC Foam

                               Nylon

                               HIPS

```html
<!DOCTYPE html>
<html lang="en">
<head>
<meta charset="utf-8">
<title>Tarvo Plastics – Business Card</title>
<link rel="stylesheet" href="https://fonts.googleapis.com/css2?family=Open+Sans:ital,wght@0,400;0,600;0,700;0,800;1,700&display=swap">
<style>
  :root{
    --navy:#1b2a5c;
    --sky:#2e8ccf;
    --orange:#f0a21f;
    --accent:#e8772e;
    --ink:#3b3b3b;
    --white:#ffffff;
    --bg:#e6e7ec;
  }
  *{box-sizing:border-box;margin:0;padding:0}
  html,body{width:1200px;height:987px;overflow:hidden;background:var(--bg)}
  body{font-family:"Open Sans",Arial,sans-serif;position:relative}
  .card{position:absolute;left:210px;width:780px;height:446px;border-radius:34px;overflow:hidden;box-shadow:0 8px 24px rgba(0,0,0,.18)}
  .card--front{top:30px;background:var(--white)}
  .card--back{top:511px;background:var(--navy);color:var(--white)}
  .card__wave{position:absolute;inset:0}

  /* front */
  .brand{position:absolute;font-weight:800;letter-spacing:-1px;line-height:1}
  .card--front .brand{left:44px;top:30px;font-size:70px;color:var(--navy)}
  .person{position:absolute;left:48px;top:118px;font-size:22px;font-weight:700;color:var(--navy)}
  .person__title{color:var(--accent);font-weight:600}
  .contact{position:absolute;left:48px;top:156px;font-size:16px;color:var(--ink);line-height:25px;list-style:none}
  .contact li{display:flex;align-items:center;gap:8px}
  .contact svg{width:14px;height:14px;fill:var(--accent);flex:none}
  .contact .gap{margin-left:18px}
  .company{position:absolute;left:48px;top:238px;font-size:14px;color:var(--ink);line-height:20px}
  .address{position:absolute;right:190px;top:360px;text-align:right;font-size:17px;line-height:24px;color:var(--white);font-style:normal}

  /* back */
  .card--back .brand{right:44px;top:30px;font-size:58px;color:var(--white)}
  .offer{position:absolute;left:0;right:0;top:106px;text-align:center;font-weight:700;font-style:italic;font-size:18px;line-height:24px}
  .col{position:absolute;top:170px}
  .col--services{left:40px;width:400px}
  .col--materials{left:490px;width:260px}
  .col__head{color:var(--orange);font-weight:700;font-size:22px;margin-bottom:6px}
  .col ul{list-style:none;font-size:16px;line-height:23px}
  .col li::before,.dot::before{content:"";display:inline-block;width:7px;height:7px;border-radius:50%;background:var(--orange);margin-right:8px;vertical-align:middle}
  .dot{margin-left:14px}
  .divider{position:absolute;left:460px;top:180px;width:1px;height:220px;background:rgba(255,255,255,.45)}
</style>
</head>
<body>

<section class="card card--front" aria-label="Card front">
  <svg class="card__wave" viewBox="0 0 780 446" aria-hidden="true">
    <path d="M0,306 C120,350 250,348 420,346 C580,344 690,366 750,446 L0,446 Z" fill="var(--navy)"/>
    <path d="M0,296 C120,340 250,338 420,336 C580,334 700,356 762,446" fill="none" stroke="var(--sky)" stroke-width="7"/>
  </svg>
  <div class="brand">Tarvo Plastics</div>
  <div class="person">Your Name, <span class="person__title">Title</span></div>
  <ul class="contact">
    <li><svg viewBox="0 0 24 24"><path d="M6.6 10.8a15 15 0 0 0 6.6 6.6l2.2-2.2a1 1 0 0 1 1-.25 11.4 11.4 0 0 0 3.6.57 1 1 0 0 1 1 1V20a1 1 0 0 1-1 1A17 17 0 0 1 3 4a1 1 0 0 1 1-1h3.5a1 1 0 0 1 1 1c0 1.25.2 2.450.57 3.57a1 1 0 0 1-.25 1z"/></svg>08 9400 4811</li>
    <li><svg viewBox="0 0 24 24"><path d="M7 1h10a2 2 0 0 1 2 2v18a2 2 0 0 1-2 2H7a2 2 0 0 1-2-2V3a2 2 0 0 1 2-2zm0 3v14h10V4z"/></svg>123-456-7890
      <svg class="gap" viewBox="0 0 24 24"><path d="M6 2h10v5H6zM3 8h18v10h-3v4H6v-4H3zm5 8v4h8v-4z"/></svg>08 9400 4822</li>
    <li><svg viewBox="0 0 24 24"><path d="M2 5h20v14H2zm2 2v.5l8 5 8-5V7z"/></svg>sales@tarvoplastics.com.au</li>
  </ul>
  <div class="company">Kelmont Holdings Pty Ltd<br>T/A Tarvo Plastics ABN: TBA</div>
  <address class="address">Unit 4/18 Kestrel Circuit<br>Canning Vale WA 6155<br>PO Box 2275 Canning Vale DC WA 6970</address>
</section>

<section class="card card--back" aria-label="Card back">
  <div class="brand">Tarvo Plastics</div>
  <p class="offer">The Products And Services That We Offer<br>Are Supplied From DIY To Trade &amp; Industrial Engineering Markets</p>
  <div class="col col--services">
    <h2 class="col__head">We specialise in:</h2>
    <ul>
      <li>Cut to size panels (all shapes and sizes)</li>
      <li>Plastics fabrication &amp; Welding</li>
      <li>Custom Designs</li>
      <li>Plastic Repairs</li>
      <li>PVC Pipe Slotting &amp; PVC Pipe Threading</li>
      <li>Supplier of all types of engineering plastics and profiles</li>
    </ul>
  </div>
  <div class="divider" aria-hidden="true"></div>
  <div class="col col--materials">
    <h2 class="col__head">Including:</h2>
    <ul>
      <li>Acrylic / Clarvene</li>
      <li>Polycarbonate / Dorvil</li>
      <li>Prismatic Light Diffuser</li>
      <li>Vantrib <span class="dot">HDPE / UHMWPE</span></li>
      <li>PVC / PVC Foam</li>
      <li>Nylon <span class="dot">HIPS</span></li>
    </ul>
  </div>
</section>

</body>
</html>
```